Detail Shop Business card design

i need a business card design for my new detailing company called 'Brisk's Polish Works'. i want an all black and white design . simple, direct and to the point. i want the designer to choose a fitting font to match the logothe front should have logo, address, phone and email and the back side should have a slogan and text indicating that we offer services on anything including cars, trucks, motorcycles and RVs. slogan will read "we take pride in your ride"
maybe also very small on the back side the IG icon with Brisks_Polish_Works

phone 208.417.6352
address 3847 E Larkin Ave
Spokane WA 99214
email: BrisksPolish@mailvexo.com

Target Market(s)

all ages , auto enthusiasts

Industry/Entity Type

Automotive

Contact Information for Business Card

the front should have logo, address, phone and email and the back side should have a slogan and text indicating that we offer services on anything including cars, trucks, motorcycles and RVs. slogan will read "we take pride in your ride"

phone 208.417.6352
address 3847 E Larkin Ave
Spokane WA 99214

Colors
000000
ffffff

Requirements
Must have
• bold font and very simple design with good spacing
Nice to have
• anything creative from the designer indicating we service any types of vehicles
Should not have
• any colors ,

```html
<!DOCTYPE html>
<html lang="en">
<head>
<meta charset="utf-8">
<title>Brisk's Polish Works – Business Cards</title>
<link href="https://fonts.googleapis.com/css2?family=Roboto+Condensed:wght@400;700&family=Oswald:wght@400;600&display=swap" rel="stylesheet">
<style>
  :root {
    --backdrop: #262626;
    --card-light: #f2f2f2;
    --card-dark: #1f1f21;
    --ink: #111111;
    --ink-soft: #555555;
    --paper: #ffffff;
  }
  * { margin: 0; padding: 0; box-sizing: border-box; }
  html, body { width: 1200px; height: 960px; overflow: hidden; }
  body {
    background: var(--backdrop);
    position: relative;
    font-family: "Roboto Condensed", "Arial Narrow", sans-serif;
  }
  .card {
    position: absolute;
    width: 600px;
    height: 343px;
    text-align: center;
  }
  .card--front { left: 314px; top: 113px; background: var(--card-light); color: var(--ink); }
  .card--back { left: 312px; top: 472px; background: var(--card-dark); color: var(--paper); }

  .brand-mark {
    position: absolute;
    left: 0; right: 0;
    display: flex;
    align-items: center;
    justify-content: center;
    gap: 12px;
    font-family: "Oswald", sans-serif;
    font-weight: 600;
    text-transform: uppercase;
    letter-spacing: 1px;
  }
  .brand-mark__dot { border-radius: 50%; }
  .card--front .brand-mark { top: 98px; font-size: 28px; color: var(--ink); }
  .card--front .brand-mark__dot { width: 18px; height: 18px; background: var(--ink); }
  .card--back .brand-mark { top: 118px; font-size: 44px; color: var(--paper); }
  .card--back .brand-mark__dot { width: 26px; height: 26px; background: var(--paper); }

  .person { position: absolute; top: 165px; left: 0; right: 0; }
  .person__name { font-size: 27px; font-weight: 700; line-height: 1; color: var(--ink); }
  .person__role { font-size: 15px; color: var(--ink-soft); margin-top: 3px; }

  .contact {
    position: absolute; top: 227px; left: 0; right: 0;
    font-size: 14px; line-height: 19px; color: var(--ink-soft);
  }

  .slogan {
    position: absolute; top: 270px; left: 136px; width: 324px;
    font-size: 17px; font-weight: 700; letter-spacing: 0.5px;
    padding-bottom: 2px;
    border-bottom: 1.5px solid var(--paper);
  }
  .services {
    position: absolute; top: 296px; left: 0; right: 0;
    font-family: "Oswald", sans-serif; font-size: 14px; font-weight: 400;
    letter-spacing: 0.2px;
  }
</style>
</head>
<body>
  <section class="card card--front" aria-label="Card front">
    <div class="brand-mark"><span class="brand-mark__dot"></span>Brisk's Polish Works</div>
    <div class="person">
      <h1 class="person__name">DALE MERCER</h1>
      <p class="person__role">CEO/FOUNDER</p>
    </div>
    <div class="contact">
      <p>3847 E Larkin Ave, Spokane WA 99214</p>
      <p>P: 208.417.6352&nbsp; M: 208 553 7140&nbsp; BrisksPolish@mailvexo.com</p>
      <p>www.briskspolish.com</p>
    </div>
  </section>

  <section class="card card--back" aria-label="Card back">
    <div class="brand-mark"><span class="brand-mark__dot"></span>Brisk's Polish Works</div>
    <p class="slogan">WE TAKE PRIDE IN YOUR RIDE</p>
    <p class="services">we offer services on anything including cars, trucks, motorcycles &amp; RVs</p>
  </section>
</body>
</html>
```